Fernway goods

Organic ethical yoga/activewear that supports kids in need and other community projects by donating % of all sales to these causes. See the product and the brand (Tamrin project) story and catalogue on
Fernwaygoods.com.au
http://files.brisvault.net/doc/q7k2m9_a41c88e0b3d94f27a615c0e2d9b7f443.pdf
Flyer is for fernway goods as the distributor for Tamrin clothing
Would like the flyer to be simple with core message and contact and site details but have a similar feel to the catalogue using some of the art graphics and or photo from site for colour. Also for wholesale/distributor enquiries or to arrange an appointment for a brand presentation contact Marla Quint 0512
Updates
I have four that I am considering so please don't submit any more. One of these will be suitable. Thanks for your submissions.
Marla
Target Market(s)
Yoga studios, wellness centres , private parties, gyms, agents
Industry/Entity Type
Clothing
Look and feel
Each slider illustrates characteristics of the customer's brand and the style your logo design should communicate.

```html
<!DOCTYPE html>
<html lang="en">
<head>
<meta charset="utf-8">
<title>Fernway goods — Flyer</title>
<link rel="stylesheet" href="https://fonts.googleapis.com/css2?family=Amatic+SC:wght@400;700&display=swap">
<style>
  :root {
    --canvas: #ece8ea;
    --paper: #f1f0f0;
    --ink: #2b2a2c;
    --ink-soft: #4a4749;
    --band-pink: #d9bfcf;
    --band-mauve: #b893a9;
    --band-teal: #b9dcdc;
    --band-cream: #f3ece4;
    --box: #1c1b1c;
    --box-text: #f4f2f2;
  }
  * { box-sizing: border-box; margin: 0; padding: 0; }
  html, body {
    width: 1200px; height: 1000px; overflow: hidden;
    background: var(--canvas);
  }
  body { position: relative; font-family: "Amatic SC", "Arial Narrow", sans-serif; color: var(--ink); }

  .flyer {
    position: absolute; left: 275px; top: 40px;
    width: 650px; height: 920px;
    background: var(--paper);
    overflow: hidden;
  }

  .pattern-band {
    position: absolute; left: 0; width: 100%;
    background: linear-gradient(90deg, var(--band-pink), var(--band-teal) 25%, var(--band-cream) 45%, var(--band-pink) 60%, var(--band-teal) 80%, var(--band-mauve));
    opacity: .75;
  }
  .pattern-band--top { top: 0; height: 70px; }
  .pattern-band--bottom { top: 846px; height: 74px; opacity: .55; }

  .tagline {
    position: absolute; right: 20px; top: 86px;
    font-size: 22px; font-weight: 700; letter-spacing: .5px;
    color: var(--ink-soft);
  }
  .tagline-underline { position: absolute; right: 24px; top: 114px; }

  .product-grid { position: absolute; left: 0; top: 0; }

  .brand-name {
    font-family: "Amatic SC", "Arial Narrow", sans-serif;
    font-size: 22px; font-weight: 700; fill: var(--box-text);
  }

  .message-box {
    position: absolute; left: 139px; top: 734px;
    width: 378px; height: 78px;
    background: var(--box);
    color: var(--box-text);
    display: flex; flex-direction: column; justify-content: center; align-items: center;
    font-size: 24px; font-weight: 700; line-height: 1.05; letter-spacing: .5px;
    text-align: center;
  }

  .contact {
    position: absolute; top: 868px;
    font-size: 13px; font-weight: 700; line-height: 1.55;
    color: var(--ink);
  }
  .contact--enquiries { left: 28px; }
  .contact--web { left: 385px; }
  .contact--office { left: 537px; }
</style>
</head>
<body>
  <main class="flyer">
    <div class="pattern-band pattern-band--top" role="img" aria-label="Geometric tribal pattern band in pink, teal and cream"></div>

    <p class="tagline">Giving back to others daily.</p>
    <svg class="tagline-underline" width="150" height="8" viewBox="0 0 150 8" aria-hidden="true">
      <polyline points="0,4 5,1 10,7 15,1 20,7 25,1 30,7 35,1 40,7 45,1 50,7 55,1 60,7 65,1 70,7 75,1 80,7 85,1 90,7 95,1 100,7 105,1 110,7 115,1 120,7 125,1 130,7 135,1 140,7 145,1 150,4" fill="none" stroke="#4a4749" stroke-width="1.2"/>
    </svg>

    <svg class="product-grid" width="650" height="740" viewBox="0 0 650 740">
      <defs>
        <linearGradient id="tone-top" x1="0" y1="0" x2="1" y2="1"><stop offset="0" stop-color="#c7a6b8"/><stop offset="1" stop-color="#8fc3c4"/></linearGradient>
        <linearGradient id="tone-purple" x1="0" y1="0" x2="1" y2="1"><stop offset="0" stop-color="#1e1c22"/><stop offset="1" stop-color="#6b3fb8"/></linearGradient>
        <linearGradient id="tone-tank" x1="0" y1="0" x2="1" y2="1"><stop offset="0" stop-color="#7b6e62"/><stop offset="1" stop-color="#2a2b33"/></linearGradient>
        <linearGradient id="tone-centre" x1="0" y1="0" x2="1" y2="1"><stop offset="0" stop-color="#6a5a56"/><stop offset="1" stop-color="#3d3533"/></linearGradient>
        <linearGradient id="tone-tee" x1="0" y1="0" x2="1" y2="1"><stop offset="0" stop-color="#3a3a3d"/><stop offset="1" stop-color="#141416"/></linearGradient>
        <linearGradient id="tone-hoodie" x1="0" y1="0" x2="1" y2="1"><stop offset="0" stop-color="#85796f"/><stop offset="1" stop-color="#4d463f"/></linearGradient>
        <linearGradient id="tone-print" x1="0" y1="0" x2="1" y2="1"><stop offset="0" stop-color="#2f3a34"/><stop offset="1" stop-color="#8d7fb5"/></linearGradient>
      </defs>
      <polygon role="img" aria-label="Photo of a patterned top in pink and teal" fill="url(#tone-top)" points="325,104 421,200 325,296 229,200"/>
      <polygon role="img" aria-label="Photo of a purple printed skirt with black top" fill="url(#tone-purple)" points="222,207 318,303 222,399 126,303"/>
      <polygon role="img" aria-label="Photo of a black tank top with geometric print" fill="url(#tone-tank)" points="428,207 524,303 428,399 332,303"/>
      <polygon role="img" aria-label="Brand photo behind the name" fill="url(#tone-centre)" points="325,310 421,406 325,502 229,406"/>
      <text class="brand-name" x="325" y="413" text-anchor="middle">Fernway goods</text>
      <polygon role="img" aria-label="Photo of a black printed t-shirt" fill="url(#tone-tee)" points="222,413 318,509 222,605 126,509"/>
      <polygon role="img" aria-label="Photo of a grey hoodie sleeve" fill="url(#tone-hoodie)" points="428,413 524,509 428,605 332,509"/>
      <polygon role="img" aria-label="Photo of a colourful geometric print fabric" fill="url(#tone-print)" points="325,516 421,612 325,708 229,612"/>
    </svg>

    <div class="message-box">
      <span>Ethical, conscious and organic products</span>
      <span>supporting the community</span>
    </div>

    <div class="pattern-band pattern-band--bottom" role="img" aria-label="Geometric tribal pattern band in pink, teal and cream"></div>

    <p class="contact contact--enquiries">For wholesale/distributor enquiries<br>or to arrange an appointment for a brand presentation contact</p>
    <p class="contact contact--web">Fernwaygoods.com.au<br>info@fernwaygoods.com.au</p>
    <p class="contact contact--office">Head Office - Marla Quint<br>Ph. 0512 384 219</p>
  </main>
</body>
</html>
```